Maplewood Bus Card

i own a building in the bronx ny - its called "Maplewood Commons"i want a classy logo / business card - nothing too religuous but it is like a family there - its a large apartment building - colors i like dark red, black, medium shade of gray also reg business card stuff tel # 555-555-0173 address 4738 Larkwell Ave Fernbrook NY 12907 Email fijosh@aol.comslogan - " Together under one roof "i can send u a picture of the building for the backside

```html
<!DOCTYPE html>
<html lang="en">
<head>
<meta charset="utf-8">
<title>Maplewood Commons — Business Card</title>
<link rel="stylesheet" href="https://fonts.googleapis.com/css2?family=Open+Sans:wght@400;600;700&display=swap">
<style>
  :root {
    --stage: #1c1c1c;
    --card: #262626;
    --red: #d3131b;
    --light: #e6e6e6;
    --rule: #4a4a4a;
  }
  * { margin: 0; padding: 0; box-sizing: border-box; }
  html, body {
    width: 1200px; height: 900px; overflow: hidden;
    background: var(--stage);
    font-family: "Open Sans", Arial, sans-serif;
  }
  .canvas {
    position: relative; width: 1200px; height: 900px;
    display: flex; flex-direction: column; align-items: center;
    justify-content: center; gap: 50px;
  }
  .card {
    position: relative; width: 560px; height: 320px;
    background: var(--card);
    border-radius: 22px;
    box-shadow: 0 14px 30px rgba(0,0,0,.55);
  }
  .brand {
    position: absolute; color: var(--red); font-weight: 700; white-space: nowrap;
  }
  .card-front .brand {
    left: 0; right: 0; top: 110px; text-align: center; font-size: 34px;
  }
  .card-front .rule {
    position: absolute; left: 140px; right: 140px; top: 178px;
    height: 1px; background: var(--rule);
  }
  .slogan {
    position: absolute; left: 0; right: 0; top: 192px;
    text-align: center; color: var(--light);
    font-size: 17px; font-weight: 600; letter-spacing: 1.5px;
  }
  .card-back .brand {
    right: 40px; top: 72px; font-size: 30px;
  }
  .card-back .rule {
    position: absolute; left: 200px; right: 40px; top: 150px;
    height: 1px; background: var(--rule);
  }
  .address {
    position: absolute; right: 40px; top: 166px; font-style: normal;
    text-align: right; color: var(--light); font-size: 15px; line-height: 1.3;
  }
  .person { position: absolute; left: 40px; top: 196px; }
  .person-name {
    color: var(--red); font-weight: 700; font-size: 17px; letter-spacing: .3px;
  }
  .person-role { color: var(--light); font-size: 15px; margin-top: 1px; }
  .contact {
    list-style: none; margin-top: 12px; color: var(--light); font-size: 15px; line-height: 1.45;
  }
  .contact li { display: flex; align-items: center; gap: 8px; }
  .contact svg { width: 13px; height: 13px; fill: var(--red); flex: none; }
</style>
</head>
<body>
<main class="canvas">
  <section class="card card-front" aria-label="Card front">
    <div class="brand">Maplewood Commons</div>
    <div class="rule"></div>
    <p class="slogan">TOGETHER UNDER ONE ROOF</p>
  </section>

  <section class="card card-back" aria-label="Card back">
    <div class="brand">Maplewood Commons</div>
    <div class="rule"></div>
    <address class="address">4738 Larkwell Ave<br>Fernbrook NY 12907</address>
    <div class="person">
      <p class="person-name">MARCUS WHITFIELD</p>
      <p class="person-role">Managing Director</p>
      <ul class="contact">
        <li>
          <svg viewBox="0 0 24 24" aria-hidden="true"><path d="M6.6 10.8a15.2 15.2 0 0 0 6.6 6.6l2.2-2.2a1 1 0 0 1 1-.25 11.4 11.4 0 0 0 3.6.57 1 1 0 0 1 1 1V20a1 1 0 0 1-1 1A17 17 0 0 1 3 4a1 1 0 0 1 1-1h3.5a1 1 0 0 1 1 1c0 1.25.2 2.45.57 3.57a1 1 0 0 1-.25 1z"/></svg>
          555-555-0173
        </li>
        <li>
          <svg viewBox="0 0 24 24" aria-hidden="true"><path d="M2 5h20v14H2z"/><path d="M2 5l10 8 10-8v2l-10 8L2 7z" fill="#262626"/></svg>
          mavreld@quintmail.com
        </li>
      </ul>
    </div>
  </section>
</main>
</body>
</html>
```